Stationery for a private security company, "Brenmoor Security Services Ltd."

Needed is a stationery design for a private security company. The designs must show professionalism and that our company mean nothing but business. Watermark of the company logo on the letterhead page is also a must. The final design must represent innovation and professionalism. It would be great if designers could integrate the colours black and silver onto the cards and letterheads..

Thank you

```html
<!DOCTYPE html>
<html lang="en">
<head>
<meta charset="utf-8">
<title>Brenmoor Security Services Ltd. — Business Card</title>
<link rel="stylesheet" href="https://fonts.googleapis.com/css2?family=Jost:ital,wght@0,400;0,600;1,400;1,600&display=swap">
<style>
  :root {
    --backdrop: #d8d5cf;
    --card-white: #f3f3f3;
    --card-silver: #c5c3c0;
    --ink: #1f1f1f;
    --ink-soft: #6c6c6c;
    --band-black: #232323;
    --band-silver: #c9c7c4;
    --watermark: #e6e6e6;
  }
  * { margin: 0; padding: 0; box-sizing: border-box; }
  html, body {
    width: 1200px; height: 900px; overflow: hidden;
    background: var(--backdrop);
    font-family: "Jost", sans-serif;
    color: var(--ink);
  }
  .canvas { position: relative; width: 1200px; height: 900px; }

  .card {
    position: absolute;
    width: 560px; height: 320px;
    box-shadow: 0 10px 24px rgba(0,0,0,.18);
    overflow: hidden;
  }

  /* Back face */
  .card--back { left: 90px; top: 90px; background: var(--card-silver); }
  .card--back .brand {
    position: absolute; left: 0; right: 0; top: 50%;
    transform: translateY(-50%);
    display: flex; flex-direction: column; align-items: center; gap: 10px;
  }

  /* Brand lockup (name only, one colour, one weight) */
  .brand-mark {
    width: 22px; height: 22px; border-radius: 50%;
    background: var(--ink);
  }
  .brand-name {
    font-weight: 600; font-size: 17px; letter-spacing: .04em;
    color: var(--ink); text-align: center; line-height: 1.15;
  }

  /* Front face */
  .card--front { left: 550px; top: 490px; background: var(--card-white); }
  .watermark {
    position: absolute; left: 0; top: 60px; width: 330px; height: 200px;
    background: radial-gradient(ellipse at 40% 60%, var(--watermark) 0%, rgba(230,230,230,0) 70%);
  }
  .card--front .brand {
    position: absolute; right: 34px; top: 54px;
    display: flex; flex-direction: column; align-items: center; gap: 8px;
    width: 190px;
  }
  .card--front .brand-name { font-size: 15px; }

  .holder { position: absolute; left: 56px; top: 86px; }
  .holder-name { font-weight: 600; font-style: italic; font-size: 16px; line-height: 1.1; }
  .holder-title { font-style: italic; font-size: 13px; color: var(--ink-soft); }

  .contact { position: absolute; left: 34px; top: 138px; list-style: none; }
  .contact li {
    display: flex; align-items: flex-start; gap: 14px;
    font-size: 15px; line-height: 1.25; margin-bottom: 6px;
  }
  .contact svg { width: 14px; height: 14px; flex: none; margin-top: 2px; fill: var(--ink); }
  .contact .email { margin-left: -10px; }

  .edge-bands { position: absolute; left: 0; bottom: 0; width: 560px; height: 70px; }
</style>
</head>
<body>
<main class="canvas">

  <section class="card card--back" aria-label="Card back">
    <div class="brand">
      <span class="brand-mark"></span>
      <span class="brand-name">Brenmoor<br>Security Services Ltd.</span>
    </div>
  </section>

  <section class="card card--front" aria-label="Card front">
    <div class="watermark" role="img" aria-label="Faint brand watermark decoration"></div>

    <div class="holder">
      <p class="holder-name">Daniel Harrow</p>
      <p class="holder-title">President</p>
    </div>

    <ul class="contact">
      <li>
        <svg viewBox="0 0 14 14" aria-hidden="true"><path d="M7 0a5 5 0 0 0-5 5c0 3.6 5 9 5 9s5-5.4 5-9a5 5 0 0 0-5-5zm0 7a2 2 0 1 1 0-4 2 2 0 0 1 0 4z"/></svg>
        <span>000 Larkfield Ave Suite 000<br>Westbury, CA&nbsp; 90000</span>
      </li>
      <li>
        <svg viewBox="0 0 14 14" aria-hidden="true"><path d="M1 4c0-2 12-2 12 0v1.5h-3V4.3H4v1.2H1zM3 7h8l1.5 6h-11z"/></svg>
        <span>000 000 0000</span>
      </li>
      <li>
        <svg viewBox="0 0 14 14" aria-hidden="true"><path d="M4 1h6v4H4zM1 6h12v5h-2v2H3v-2H1zm3 3v3h6V9z"/></svg>
        <span>000 000 0000</span>
      </li>
      <li class="email">
        <svg viewBox="0 0 14 14" aria-hidden="true"><path d="M0 3h14v9H0zm1.2 1.2v.3L7 8.5l5.8-4v-.3zm0 1.7v4.9h11.6V5.9L7 9.9z"/></svg>
        <span>name@company.com.nz</span>
      </li>
    </ul>

    <div class="brand">
      <span class="brand-mark"></span>
      <span class="brand-name">Brenmoor<br>Security Services Ltd.</span>
    </div>

    <svg class="edge-bands" viewBox="0 0 560 70" aria-hidden="true">
      <path d="M0 12 L380 14 L380 22 L0 20 Z" fill="var(--band-black)"/>
      <path d="M0 24 L372 26 C385 26 386 8 400 8 L560 8 L560 70 L0 70 Z" fill="var(--band-silver)"/>
    </svg>
  </section>

</main>
</body>
</html>
```